Fern Lattice Table & Chair Rentals

We need a business card for a table and chair rental company. We rent tables and chairs for weddings, funerals, business events and parties. We want something that looks clean and elegant while not being too busy. We would like colors in the green and blue hues and avoiding anything orange. We want to make sure the font is large enough to be seen easily.

Target Market(s)

Wedding & Event Rentals

Industry/Entity Type

Events

Contact Information for Business Card

Fern Lattice, sales@fernlatticerentals.com, fernlatticerentals.com, 360-555-0182

Requirements
Must have
• Easy to read font
Should not have
• Orange anywhere in the design

```html
<!DOCTYPE html>
<html lang="en">
<head>
<meta charset="utf-8">
<title>Fern Lattice – Business Card</title>
<link href="https://fonts.googleapis.com/css2?family=Oxygen:wght@400;700&display=swap" rel="stylesheet">
<style>
  :root {
    --page-bg: #e8ecea;
    --card-bg: #fbfcfb;
    --band-dark: #1f3a36;
    --band-accent: #2a7a8c;
    --band-accent-light: #5fb0a0;
    --ink-dark: #23332f;
    --ink-soft: #46605a;
    --rule: #2f8a8a;
    --icon-bg: #2f6b63;
  }
  * { box-sizing: border-box; margin: 0; padding: 0; }
  html, body {
    width: 1200px; height: 818px; overflow: hidden;
    background: var(--page-bg);
    font-family: "Oxygen", sans-serif;
  }
  .card {
    position: absolute; left: 75px; top: 109px;
    width: 1050px; height: 600px;
    background: var(--card-bg);
    box-shadow: 0 10px 30px rgba(0,0,0,0.16);
    overflow: hidden;
  }
  .side-band {
    position: absolute; left: 0; top: 0; width: 62px; height: 100%;
    background: var(--band-dark);
  }
  .side-band__accent {
    position: absolute; left: 0; bottom: 0; width: 100%; height: 130px;
    background: linear-gradient(to bottom, var(--band-accent-light), var(--band-accent));
  }
  .brand { position: absolute; left: 112px; top: 64px; color: var(--ink-dark); }
  .brand__name { font-size: 56px; font-weight: 700; line-height: 1; }
  .brand__tagline { font-size: 27px; margin-top: 12px; color: var(--ink-soft); }
  .contact-name {
    position: absolute; left: 112px; top: 262px;
    font-size: 46px; font-weight: 700; color: var(--ink-soft);
  }
  .contact-list { position: absolute; left: 112px; top: 430px; list-style: none; }
  .contact-list li {
    display: flex; align-items: center; gap: 14px;
    font-size: 26px; color: var(--ink-dark); margin-bottom: 20px;
  }
  .contact-icon {
    width: 28px; height: 28px; background: var(--icon-bg);
    border-radius: 4px; display: flex; align-items: center; justify-content: center;
  }
  .hours {
    position: absolute; left: 640px; top: 60px; list-style: none;
    font-size: 26px; line-height: 1.45; color: var(--ink-dark);
  }
  .hours-rule {
    position: absolute; left: 560px; top: 300px; width: 490px; height: 3px;
    background: var(--rule);
  }
  .website {
    position: absolute; right: 60px; bottom: 60px;
    font-size: 26px; color: var(--ink-dark);
  }
</style>
</head>
<body>
  <section class="card">
    <div class="side-band"><div class="side-band__accent"></div></div>

    <header class="brand">
      <div class="brand__name">Fern Lattice</div>
      <div class="brand__tagline">Table and Chair Rentals</div>
    </header>

    <div class="contact-name">Fern Lattice</div>

    <ul class="contact-list">
      <li>
        <span class="contact-icon">
          <svg width="18" height="18" viewBox="0 0 24 24" aria-hidden="true">
            <path fill="#fff" d="M6.6 10.8a15.1 15.1 0 0 0 6.6 6.6l2.2-2.2a1 1 0 0 1 1-.25 11.4 11.4 0 0 0 3.6.57 1 1 0 0 1 1 1V20a1 1 0 0 1-1 1A17 17 0 0 1 3 4a1 1 0 0 1 1-1h3.5a1 1 0 0 1 1 1c0 1.25.2 2.45.57 3.57a1 1 0 0 1-.25 1z"/>
          </svg>
        </span>
        360-555-0182
      </li>
      <li>
        <span class="contact-icon">
          <svg width="18" height="18" viewBox="0 0 24 24" aria-hidden="true">
            <rect x="3" y="6" width="18" height="12" rx="1" fill="none" stroke="#fff" stroke-width="2"/>
            <path d="M3 7l9 6 9-6" fill="none" stroke="#fff" stroke-width="2"/>
          </svg>
        </span>
        sales@fernlatticerentals.com
      </li>
    </ul>

    <ul class="hours">
      <li>Mon-Fri: 8am to 6pm</li>
      <li>Saturday: 8am to 4pm</li>
      <li>Sunday: 9am to 1pm</li>
    </ul>
    <div class="hours-rule"></div>

    <div class="website">www.fernlatticerentals.com</div>
  </section>
</body>
</html>
```